Tolvik Commercial Cleaning is lookong for a new business card design.

A fresh new design that's professional and stylish. We need a serious upgrade to our business cards. I have included pictures of our existing ones. Our clients include professional individuals and business owners. We woupdblike something professional and upbeat. Please have fun and see what you come uo with.

Target Market(s)

Property managers, business owners, facility managers and other similar professionals

Industry/Entity Type

Janitorial

Contact Information for Business Card

Name, cell, office number, email, web address

Font styles to use
Sans Serif

Colors

Designer to choose colors to be used in the design.

Requirements
Must have
• please use the green color in our logo
Nice to have
• Bar code
Should not have
• Address

```html
<!DOCTYPE html>
<html lang="en">
<head>
<meta charset="utf-8">
<title>Tolvik Commercial Cleaning – Business Card</title>
<link href="https://fonts.googleapis.com/css2?family=Open+Sans:wght@400;600;700&display=swap" rel="stylesheet">
<style>
  :root {
    --brand-green: #39b35a;
    --brand-green-deep: #2c9a49;
    --brand-blue: #2f67ae;
    --card-white: #fdfdf4;
    --ink: #1d1d1d;
    --backdrop: #e9e6df;
  }
  * { margin: 0; padding: 0; box-sizing: border-box; }
  html, body {
    width: 1200px; height: 780px; overflow: hidden;
    background: var(--backdrop);
    font-family: "Open Sans", Arial, sans-serif;
  }
  .canvas {
    width: 1200px; height: 780px;
    display: flex; align-items: center; justify-content: center; gap: 40px;
  }
  .card {
    width: 540px; height: 309px;
    border-radius: 22px;
    position: relative;
    overflow: hidden;
    box-shadow: 0 6px 18px rgba(0,0,0,.15);
  }
  .card--front { background: var(--card-white); }
  .card--back {
    background: var(--brand-green);
    display: flex; align-items: center; justify-content: center;
  }
  .brand-name {
    font-weight: 700;
    letter-spacing: -1px;
    line-height: 1;
  }
  .card--front .brand-name {
    position: absolute; left: 44px; top: 118px;
    font-size: 58px; color: var(--brand-green);
  }
  .card--back .brand-name {
    font-size: 96px; color: var(--brand-green-deep);
  }
  .divider {
    position: absolute; left: 0; top: 0;
  }
  .person {
    position: absolute; left: 300px; top: 92px;
  }
  .person-name {
    font-weight: 700; font-size: 30px; line-height: 1.1;
    margin-bottom: 18px;
  }
  .person-name .first { color: var(--brand-green); }
  .person-name .last { color: var(--brand-blue); }
  .contact-list { list-style: none; }
  .contact-list li {
    display: flex; align-items: center; gap: 8px;
    font-size: 15px; color: var(--ink); line-height: 1.55;
  }
  .contact-list svg { flex: none; }
</style>
</head>
<body>
<main class="canvas">
  <section class="card card--front" aria-label="Business card front">
    <div class="brand-name">Tolvik</div>
    <svg class="divider" width="540" height="309" aria-hidden="true">
      <line x1="285" y1="62" x2="250" y2="262" stroke="#222" stroke-width="1"/>
    </svg>
    <div class="person">
      <h1 class="person-name"><span class="first">Dana</span> <span class="last">Whitfield</span></h1>
      <ul class="contact-list">
        <li>
          <svg width="14" height="14" viewBox="0 0 24 24" aria-hidden="true"><path fill="#39b35a" d="M6.6 10.8a15 15 0 0 0 6.6 6.6l2.2-2.2c.3-.3.7-.4 1-.2 1.1.4 2.3.6 3.6.6.6 0 1 .4 1 1V20c0 .6-.4 1-1 1A17 17 0 0 1 3 4c0-.6.4-1 1-1h3.5c.6 0 1 .4 1 1 0 1.3.2 2.5.6 3.6.1.3 0 .7-.2 1z"/></svg>
          (555) 014-2286
        </li>
        <li>
          <svg width="14" height="14" viewBox="0 0 24 24" aria-hidden="true"><rect x="2" y="5" width="20" height="14" rx="2" fill="#39b35a"/><path d="M3 6l9 7 9-7" stroke="#fff" stroke-width="1.6" fill="none"/></svg>
          dana@tolvikcleaning.com
        </li>
        <li>
          <svg width="14" height="14" viewBox="0 0 24 24" aria-hidden="true"><circle cx="12" cy="12" r="10" fill="#39b35a"/><path d="M2 12h20M12 2c3 3 3 17 0 20M12 2c-3 3-3 17 0 20" stroke="#fff" stroke-width="1.4" fill="none"/></svg>
          www.tolvikcleaning.com
        </li>
      </ul>
    </div>
  </section>

  <section class="card card--back" aria-label="Business card back">
    <div class="brand-name">Tolvik</div>
  </section>
</main>
</body>
</html>
```